Wellness, Meaning, and the Inner Journey Research Program Website

Overview: This website will serve a new research program (Wellness, Meaning, and the Inner Journey) at the Harrowgate University School of Medicine. I want a clean, intuitive design that has a navigation bar, but uses icons/graphic buttons to link to the main pages. In an attached Word document, I have provided a basic information architecture for the site, understanding that this project would just generate graphics and code for the 3 pages. I highlighted the 3 pages I'd like designed.
Target market: People who want to participate in our research, or contribute grant funding to specific projects.
Number of page: The design project focuses on 3 pages, but the site must accommodate 6 pages with top-level links. See attached Word doc.
Logo and website header: Please integrate our logo in the header. I've uploaded it as a png file--both with the name of the website and with just the logo image. I imaging the logo would look great in a banner set against an image of a mountain. The two main design themes I want to see included are nature and healthcare.
Text content: I have not yet provided text. Use some dummy text.
Technical Specifications:
- Build using WordPress. We will host this site ourselves on NetHarbor using WordPress.
- The design package must be coded.
- The template must be responsive to different platforms (e.g., computer, mobile phone, iPad).
Thank you! I look forward to seeing your designs.
- Ned

```html
<!DOCTYPE html>
<html lang="en">
<head>
<meta charset="utf-8">
<title>Wellness, Meaning, and the Inner Journey – The Research Program</title>
<link href="https://fonts.googleapis.com/css2?family=Roboto:wght@400;500;700&family=Rubik:wght@500;700&display=swap" rel="stylesheet">
<style>
:root{
  --blue:#0f4582;
  --blue-dark:#0c3a70;
  --green:#5f9a26;
  --green-light:#73ad2e;
  --white:#ffffff;
  --text:#222222;
  --muted:#444444;
}
*{box-sizing:border-box;margin:0;padding:0}
html,body{width:1200px;height:3338px;overflow:hidden;background:var(--white)}
body{position:relative;font-family:'Roboto',sans-serif;color:var(--text)}
.abs{position:absolute}
a{color:inherit;text-decoration:none}
svg{display:block}

/* header */
.brand{left:143px;top:18px;display:flex;align-items:center;gap:10px}
.brand-mark{width:38px;height:38px;border-radius:50%;background:var(--green)}
.brand-name{font-weight:700;font-size:13px;color:var(--blue);line-height:1.2}
.brand-name small{display:block;font-size:11px;color:var(--blue)}
.call{left:758px;top:12px;width:192px;height:47px;border:2px solid var(--blue);border-radius:24px;display:flex;align-items:center;gap:10px;padding-left:12px;font-weight:700;font-size:13px;color:var(--blue)}
.call-ico{width:28px;height:28px;border-radius:50%;border:2px solid var(--green);display:flex;align-items:center;justify-content:center}
.lang{left:973px;top:21px;width:64px;height:29px;border:1px solid #ddd;display:flex;align-items:center;justify-content:center;gap:8px}
.flag{width:26px;height:14px;background:linear-gradient(#b22 0 50%,#fff 50% 60%,#b22 60%);position:relative}
.flag::before{content:"";position:absolute;left:0;top:0;width:11px;height:8px;background:#2a3f8f}
.nav{left:162px;top:78px;width:876px;height:64px;background:var(--green);border-radius:32px;display:flex;align-items:center;z-index:3;font-weight:700;font-size:16px;color:var(--white)}
.nav a{margin-right:42px}
.nav .home{background:var(--blue);height:64px;width:131px;border-radius:32px;display:flex;align-items:center;justify-content:center;margin-right:32px}

/* hero */
.hero{left:0;top:107px;width:1200px;height:680px;background:linear-gradient(100deg,#b9643f 0%,#8a5a8c 25%,#5b6bc9 55%,#3a4fbf 80%,#5060c8 100%);overflow:hidden}
.hero-figure{left:140px;top:40px;width:420px;height:620px;background:radial-gradient(ellipse at 50% 40%,#1f6b4a 0%,#2c7a55 45%,rgba(44,122,85,0) 70%)}
.hero-title{left:553px;top:235px;font-family:'Rubik',sans-serif;font-weight:700;font-size:63px;line-height:76px;color:var(--white);letter-spacing:1px;text-shadow:0 3px 8px rgba(0,0,0,.35);white-space:nowrap}
.btn-start{left:555px;top:493px;width:182px;height:68px;border-radius:34px;background:var(--blue);color:var(--white);font-weight:700;font-size:16px;display:flex;align-items:center;justify-content:center}
.dots{left:1118px;top:392px;display:flex;flex-direction:column;gap:17px}
.dots i{width:8px;height:8px;border-radius:50%;background:var(--white)}
.dots i.on{background:var(--green-light)}
.hero-curve{left:0;top:680px;width:1200px;height:110px}

/* people */
.h2{width:1200px;left:0;text-align:center;font-family:'Rubik',sans-serif;font-weight:700;font-size:44px;color:var(--blue)}
.h2 span{color:var(--green)}
.tabs{left:236px;top:942px;display:flex;gap:9px}
.tab{height:67px;border:2px solid #9db0cc;border-radius:34px;display:flex;align-items:center;justify-content:center;font-weight:700;font-size:16px;color:var(--blue)}
.tab.active{background:var(--blue);border-color:var(--blue);color:var(--white)}
.person{width:280px;text-align:center}
.ring{width:242px;height:242px;border:2px solid var(--green);border-radius:50%;margin:0 auto;position:relative;display:flex;align-items:center;justify-content:center}
.portrait{width:190px;height:190px;border-radius:50%}
.badge{position:absolute;left:50%;bottom:-10px;transform:translateX(-50%);width:48px;height:48px;border-radius:50%;background:var(--blue);color:var(--white);font-weight:700;font-size:15px;display:flex;align-items:center;justify-content:center;border:3px solid var(--green)}
.person h3{margin-top:40px;font-weight:500;font-size:20px;color:var(--text)}
.person p{margin-top:10px;font-size:13px;line-height:22px;color:var(--muted)}

/* projects */
.projects{left:0;top:1566px;width:1200px;height:838px;background:var(--green);overflow:hidden}
.projects > svg{position:absolute;left:0;top:0}
.projects .h2{color:var(--white);top:80px}
.card{width:448px;height:247px;border-radius:4px;display:flex;align-items:flex-end;justify-content:center;padding-bottom:26px;font-weight:500;font-size:20px;color:var(--white)}
.arrow{width:46px;height:46px;border-radius:50%;border:2px solid var(--white);display:flex;align-items:center;justify-content:center}

/* faqs */
.faq{height:68px;border:2px solid var(--green);border-radius:34px;display:flex;align-items:center;justify-content:space-between;padding:0 12px 0 34px;font-weight:500;font-size:15px;line-height:22px;color:var(--text)}
.faq-go{width:44px;height:44px;border-radius:50%;background:var(--blue);flex:none;display:flex;align-items:center;justify-content:center}

/* footer */
.footer{left:0;top:2860px;width:1200px;height:478px;background:var(--blue);color:var(--white)}
.footer-curve{position:absolute;left:0;top:-2px}
.fcol{position:absolute;top:165px}
.fcol h4{font-weight:500;font-size:17px;margin-bottom:25px}
.fcol li{list-style:none;font-size:14px;line-height:24px}
.fcol li::before{content:"»";margin-right:16px}
.contact-row{display:flex;gap:16px;font-size:14px;line-height:20px;margin-bottom:22px}
.social{display:flex;gap:10px}
.social span{width:34px;height:34px;border:2px solid var(--white);border-radius:50%;display:flex;align-items:center;justify-content:center;font-size:11px;font-weight:700}
.pay{display:flex;gap:8px;margin-top:14px}
.pay span{height:28px;padding:0 6px;background:var(--white);color:var(--blue);font-size:11px;font-weight:700;display:flex;align-items:center}
.rule{left:90px;top:397px;width:1020px;height:1px;background:rgba(255,255,255,.15)}
.copy{left:0;top:434px;width:1200px;text-align:center;font-size:14px}
.totop{left:16px;top:422px;width:47px;height:47px;background:var(--green);display:flex;align-items:center;justify-content:center}
</style>
</head>
<body>

<header>
  <div class="abs brand">
    <span class="brand-mark"></span>
    <div class="brand-name">Wellness, Meaning, and the Inner Journey<small>The Research Program</small></div>
  </div>
  <a class="abs call" href="#"><span class="call-ico"><svg width="14" height="14" viewBox="0 0 24 24"><path d="M6.6 10.8a15 15 0 0 0 6.6 6.6l2.2-2.2a1 1 0 0 1 1-.25 11.4 11.4 0 0 0 3.6.57 1 1 0 0 1 1 1V20a1 1 0 0 1-1 1A17 17 0 0 1 3 4a1 1 0 0 1 1-1h3.5a1 1 0 0 1 1 1c0 1.25.2 2.45.57 3.57a1 1 0 0 1-.25 1z" fill="#5f9a26"/></svg></span>Call 1 888 888 8888</a>
  <div class="abs lang"><span class="flag"></span><svg width="8" height="5"><path d="M0 0h8L4 5z" fill="#333"/></svg></div>
  <nav class="abs nav">
    <a class="home" href="#">HOME</a>
    <a href="#">PEOPLE</a><a href="#">PROJECTS</a><a href="#">FAQS</a><a href="#">RESOURCES</a><a href="#">CONTACT</a>
    <svg width="17" height="17" viewBox="0 0 20 20"><circle cx="8" cy="8" r="6" stroke="#fff" stroke-width="3" fill="none"/><path d="M12.5 12.5 18 18" stroke="#fff" stroke-width="3"/></svg>
  </nav>
</header>

<section class="abs hero" role="img" aria-label="Woman in a green dress sitting on rocks by the sea with closed eyes, sunlight glowing at her head">
  <div class="abs hero-figure"></div>
</section>
<h1 class="abs hero-title">WELLNESS,<br>MEANING &amp; THE<br>INNER JOURNEY</h1>
<a class="abs btn-start" href="#">GET STARTED</a>
<div class="abs dots"><i></i><i class="on"></i><i></i><i></i></div>
<svg class="abs hero-curve" viewBox="0 0 1200 110" preserveAspectRatio="none">
  <path d="M0 100 Q320 95 600 12 Q880 95 1200 100 L1200 110 L0 110Z" fill="#5f9a26"/>
  <path d="M0 108 Q320 103 600 22 Q880 103 1200 98 L1200 110 L0 110Z" fill="#fff"/>
</svg>

<section>
  <h2 class="abs h2" style="top:836px">Our <span>People</span></h2>
  <div class="abs tabs">
    <a class="tab active" style="width:221px" href="#">RESEARCH TEAM</a>
    <a class="tab" style="width:268px" href="#">ADVISORY COMMITTEE</a>
    <a class="tab" style="width:220px" href="#">PARTNERS</a>
  </div>
  <div class="abs person" style="left:124px;top:1116px">
    <div class="ring"><div class="portrait" role="img" aria-label="Portrait of a smiling man in a striped shirt at a cafe" style="background:radial-gradient(circle at 50% 40%,#c9a98d,#5a4a3a 70%,#2e2a26)"></div><span class="badge">Lw</span></div>
    <h3>JOHNDOE</h3><p>Sed ut perspiciatis unmnis<br>iste natus</p>
  </div>
  <div class="abs person" style="left:459px;top:1116px">
    <div class="ring"><div class="portrait" role="img" aria-label="Portrait of a smiling woman working on a laptop" style="background:radial-gradient(circle at 50% 40%,#e2c9a8,#b9b3a8 60%,#8d8a84)"></div><span class="badge">Lw</span></div>
    <h3>DIANE MORROW</h3><p>Sed ut perspiciatis unmnis<br>iste natus</p>
  </div>
  <div class="abs person" style="left:795px;top:1116px">
    <div class="ring"><div class="portrait" role="img" aria-label="Portrait of a businessman in a suit reading a tablet" style="background:radial-gradient(circle at 50% 40%,#c7a88a,#3e4352 60%,#cfd4da)"></div><span class="badge">Lw</span></div>
    <h3>YURI GRANT</h3><p>Sed ut perspiciatis unmnis<br>iste natus</p>
  </div>
</section>

<section class="abs projects">
  <svg width="1200" height="838" viewBox="0 0 1200 838"><path d="M0 0H1200L582 838Z" fill="#0f4582"/></svg>
  <h2 class="abs h2">Projects</h2>
  <div class="abs card" style="left:144px;top:178px;background:linear-gradient(180deg,#c9c6cf,#8a8580 50%,#1a1a1a)" role="img" aria-label="Silhouette of a woman raising her arms against a misty sky">PROJECT NAME</div>
  <div class="abs card" style="left:608px;top:178px;background:linear-gradient(180deg,#5a5a5e,#2e2e32 60%,#161616)" role="img" aria-label="Surreal head profile with a doorway and a small standing figure">PROJECT NAME</div>
  <div class="abs card" style="left:144px;top:443px;background:radial-gradient(circle at 50% 40%,#1f3a7a,#0d1540 55%,#0a0a14)" role="img" aria-label="Meditating figure within a glowing geometric mandala">PROJECT NAME</div>
  <div class="abs card" style="left:608px;top:443px;background:linear-gradient(160deg,#8a6d5c,#d7b894 40%,#6a5040 75%,#1c1410)" role="img" aria-label="Hands holding a glass jar as butterflies fly out">PROJECT NAME</div>
  <a class="abs arrow" style="left:955px;top:748px" href="#"><svg width="12" height="18" viewBox="0 0 12 18"><path d="M9 2 2 9l7 7" stroke="#fff" stroke-width="2.5" fill="none"/></svg></a>
  <a class="abs arrow" style="left:1010px;top:748px" href="#"><svg width="12" height="18" viewBox="0 0 12 18"><path d="M3 2l7 7-7 7" stroke="#fff" stroke-width="2.5" fill="none"/></svg></a>
</section>

<section>
  <h2 class="abs h2" style="top:2497px">FAQs</h2>
  <a class="abs faq" style="left:145px;top:2609px;width:451px" href="#">WHAT MAKES THIS PROJECT UNIQUE?<span class="faq-go"><svg width="16" height="16"><circle cx="8" cy="8" r="7" fill="#fff"/><path d="M4 8h7M8 5l3 3-3 3" stroke="#0f4582" stroke-width="2" fill="none"/></svg></span></a>
  <a class="abs faq" style="left:605px;top:2609px;width:450px" href="#">DOES THIS PROJECT ASSUME THAT THE<br>IMPACT OF RELIGION IS ALWAYS POSITIVE?<span class="faq-go"><svg width="16" height="16"><circle cx="8" cy="8" r="7" fill="#fff"/><path d="M4 8h7M8 5l3 3-3 3" stroke="#0f4582" stroke-width="2" fill="none"/></svg></span></a>
  <a class="abs faq" style="left:145px;top:2704px;width:451px" href="#">HOW CAN I COLLABORATE?<span class="faq-go"><svg width="16" height="16"><circle cx="8" cy="8" r="7" fill="#fff"/><path d="M4 8h7M8 5l3 3-3 3" stroke="#0f4582" stroke-width="2" fill="none"/></svg></span></a>
  <a class="abs faq" style="left:605px;top:2704px;width:450px" href="#">WILL HGU FACULTY LEAD ALL PROJECTS?<span class="faq-go"><svg width="16" height="16"><circle cx="8" cy="8" r="7" fill="#fff"/><path d="M4 8h7M8 5l3 3-3 3" stroke="#0f4582" stroke-width="2" fill="none"/></svg></span></a>
</section>

<footer class="abs footer">
  <svg class="footer-curve" width="1200" height="100" viewBox="0 0 1200 100">
    <path d="M0 0H1200V8Q880 14 600 80Q320 14 0 8Z" fill="#5f9a26"/>
    <path d="M0 0H1200V2Q880 4 600 68Q320 4 0 2Z" fill="#fff"/>
  </svg>
  <div class="fcol" style="left:142px"><h4>QUICK LINKS</h4><ul><li>Home</li><li>People</li><li>Projects</li><li>FAQs</li><li>Resources</li><li>Contact us</li></ul></div>
  <div class="fcol" style="left:320px"><h4>OTHER LINKS</h4><ul><li>Terms and Use</li><li>Privacy Policy</li><li>Information</li><li>Sitemap</li></ul></div>
  <div class="fcol" style="left:528px"><h4>CONTACT US</h4>
    <div class="contact-row"><svg width="14" height="18" viewBox="0 0 14 18"><path d="M7 17S1 10 1 6.5a6 6 0 0 1 12 0C13 10 7 17 7 17z" stroke="#fff" fill="none"/><circle cx="7" cy="6.5" r="2" stroke="#fff" fill="none"/></svg><span>123 Sample Street, Sample City,<br>New State, USA</span></div>
    <div class="contact-row"><svg width="16" height="16" viewBox="0 0 24 24"><path d="M6.6 10.8a15 15 0 0 0 6.6 6.6l2.2-2.2 4.6 1V20A17 17 0 0 1 3 4h4.5l1 4.6z" stroke="#fff" fill="none" stroke-width="1.5"/></svg><span>(+1) 888 888 8888</span></div>
    <div class="contact-row"><svg width="16" height="12" viewBox="0 0 16 12"><rect x=".5" y=".5" width="15" height="11" stroke="#fff" fill="none"/><path d="M.5.5 8 7l7.5-6.5" stroke="#fff" fill="none"/></svg><span>contact@companyname.com</span></div>
  </div>
  <div class="fcol" style="left:840px"><h4>SOCIAL MEDIA</h4>
    <div class="social"><span>Kn</span><span>Ch</span><span>Pn</span><span>Sg</span><span>Lw</span></div>
    <h4 style="margin-top:30px;margin-bottom:0">MAKE PAYMENT</h4>
    <div class="pay"><span>Payvia</span><span>Cardmix</span><span>Swiftpay</span><span>Amplex</span></div>
  </div>
  <div class="abs rule"></div>
  <p class="abs copy">© Copyright 2021 Companyname. All Rights Reserved &nbsp;|&nbsp; Privacy Policy</p>
  <a class="abs totop" href="#"><svg width="24" height="22" viewBox="0 0 24 22"><path d="M3 11 12 3l9 8M3 19l9-8 9 8" stroke="#fff" stroke-width="3" fill="none"/></svg></a>
</footer>

</body>
</html>
```